need corporate, modern business card created for Consulting Company

I need a slick business card using elements from my website, as well as, integrating my pixelforge-created logo (see files).

The business card needs to be:
1. Corporate and modern
2. Clean and professional

I've included a PSD with the logo/icon that you can use to create it. Feel free to try a metallic finish on the logo, make it bigger/small, underlay it. Whatever you need to do to make my card stand out.

Try a black background, or white background or gray.

The idea is for my card to be memorable as well as professional and corporate.

Target Market(s)

Corporate business in the US and Canada.

Industry/Entity Type

Business

Contact Information for Business Card

Commerce Advancing Methods
Martin Coles, Senior Partner
office: 1 877 555 0143
mobile: 1 519 555 0172
website: http://www.brightvale.example

Requirements
Must have
• Card-related information
• corporate, yet modern
• clean and professional
• incorporate the icon only
• must have an editable form when complete!
Nice to have
• metallic icon might be cool
• try it with white or black

```html
<!DOCTYPE html>
<html lang="en">
<head>
<meta charset="UTF-8">
<title>Brightvale Business Card</title>
<link rel="stylesheet" href="https://fonts.googleapis.com/css2?family=Open+Sans:wght@400;600;700&display=swap">
<style>
  :root {
    --backdrop: #a9adb3;
    --card-black: #1f1f20;
    --brand-blue: #316bbd;
    --swoosh-white: #ffffff;
    --swoosh-gray: #b4b6ba;
    --text-light: #ffffff;
  }
  * { margin: 0; padding: 0; box-sizing: border-box; }
  html, body {
    width: 1200px;
    height: 866px;
    overflow: hidden;
  }
  body {
    background: var(--backdrop);
    font-family: "Open Sans", Arial, sans-serif;
  }
  .canvas {
    width: 1200px;
    height: 866px;
    display: flex;
    flex-direction: column;
    align-items: center;
    justify-content: center;
    gap: 40px;
  }
  .card {
    position: relative;
    width: 640px;
    height: 366px;
    overflow: hidden;
    box-shadow: 0 10px 24px rgba(0, 0, 0, 0.28);
  }
  .card-front {
    background: var(--card-black);
    display: flex;
    align-items: center;
    justify-content: center;
  }
  .brand {
    display: flex;
    align-items: center;
    gap: 14px;
    color: var(--brand-blue);
    font-weight: 600;
    letter-spacing: -0.5px;
  }
  .brand-dot {
    display: block;
    border-radius: 50%;
    background: var(--brand-blue);
  }
  .card-front .brand { font-size: 62px; }
  .card-front .brand-dot { width: 34px; height: 34px; }

  .card-back { background: var(--brand-blue); }
  .card-back .swoosh {
    position: absolute;
    inset: 0;
    width: 100%;
    height: 100%;
  }
  .card-back .brand {
    position: absolute;
    left: 44px;
    bottom: 62px;
    font-size: 34px;
    gap: 9px;
  }
  .card-back .brand-dot { width: 18px; height: 18px; }

  .details {
    position: absolute;
    right: 30px;
    top: 30px;
    text-align: right;
    color: var(--text-light);
    font-size: 15px;
    line-height: 1.3;
  }
  .holder-name { font-weight: 700; font-size: 17px; }
  .holder-role { font-size: 16px; margin-bottom: 46px; }
  .address { margin-bottom: 28px; }
  .contact-line {
    display: flex;
    justify-content: flex-end;
    align-items: center;
    gap: 6px;
  }
  .contact-line svg {
    width: 13px;
    height: 13px;
    fill: var(--text-light);
  }
</style>
</head>
<body>
<main class="canvas">

  <section class="card card-front" aria-label="Card front">
    <div class="brand"><span class="brand-dot"></span>brightvale</div>
  </section>

  <section class="card card-back" aria-label="Card back">
    <svg class="swoosh" viewBox="0 0 640 366" preserveAspectRatio="none" aria-hidden="true">
      <path d="M0,0 H205 C380,70 400,250 345,366 H0 Z" fill="var(--swoosh-gray)"/>
      <path d="M0,0 H185 C362,66 382,250 326,366 H0 Z" fill="var(--swoosh-white)"/>
      <path d="M0,0 H172 C350,64 372,250 316,366 H0 Z" fill="var(--brand-blue)"/>
      <path d="M0,0 H160 C338,62 360,250 304,366 H0 Z" fill="var(--card-black)"/>
    </svg>

    <div class="brand"><span class="brand-dot"></span>brightvale</div>

    <div class="details">
      <p class="holder-name">Dana Whitfield</p>
      <p class="holder-role">Consultant</p>
      <p class="address">041.12th floor,Park<br>Harbour Road KLM</p>
      <p class="contact-line">012 345 6789
        <svg viewBox="0 0 24 24"><path d="M6.6 10.8a15.1 15.1 0 0 0 6.6 6.6l2.2-2.2a1 1 0 0 1 1-.25 11.4 11.4 0 0 0 3.6.57 1 1 0 0 1 1 1V20a1 1 0 0 1-1 1A17 17 0 0 1 3 4a1 1 0 0 1 1-1h3.5a1 1 0 0 1 1 1c0 1.25.2 2.45.57 3.57a1 1 0 0 1-.25 1Z"/></svg>
      </p>
      <p class="contact-line">012 345 6789
        <svg viewBox="0 0 24 24"><path d="M6 2h9l3 3v5H6Z M3 11h18v9H3Z M7 14h4v2H7Z M14 13h2v2h-2Z M17 13h2v2h-2Z M14 16h2v2h-2Z M17 16h2v2h-2Z"/></svg>
      </p>
      <p class="contact-line">urname@email.com
        <svg viewBox="0 0 24 24"><path d="M2 5h20v14H2Z M3.5 6.5 12 13l8.5-6.5Z" fill-rule="evenodd"/></svg>
      </p>
      <p class="contact-line">www.yourwebsitename.com</p>
    </div>
  </section>

</main>
</body>
</html>
```